Lush Satchel

I am developing a web site which sells preowned high end designer handbags and accessories. Some of the brands include: Varenne, Marcel Ostrand & Belmo, to name a few. I am after a luxurious and high end feel.

Some brands I like that express this feel include: Quintel, Belmo, fabcloset.com, pursepassonpaw.com

I am after a logo, business card, letterhead, with compliments, address label and envelope designs.
The business name is Lush satchel, and the website will be www.lushsatchel.com.au. I have thoughts of using LSC as a logo or LUSH satchel.com.au

I don't want a large logo, it needs to blend in with the name in some way - or may not need an image at all, if the style of the font speaks to the brand.

Thank-you
Updates

Project Deadline Extended
Reason: I would like to give designers plenty of time to be able to submit a design.

Target Market(s)

Women, aged 25-60 who are into fashion

Industry/Entity Type

Business

Requirements
Must have
• High End
Luxurious

```html
<!DOCTYPE html>
<html lang="en">
<head>
<meta charset="utf-8">
<title>Lush Satchel – Business Card Concepts</title>
<link rel="stylesheet" href="https://fonts.googleapis.com/css2?family=Source+Sans+3:wght@400;600&family=Arimo:wght@700&display=swap">
<style>
  :root {
    --crimson: #c01f41;
    --ink: #000000;
    --paper: #ffffff;
  }
  html, body {
    margin: 0;
    padding: 0;
    width: 1200px;
    height: 1033px;
    overflow: hidden;
    background: var(--paper);
  }
  .sheet {
    display: block;
    width: 1200px;
    height: 1033px;
  }
  .card-edge { fill: none; stroke: var(--ink); stroke-width: 2; }
  .card-fill { fill: var(--crimson); }
  .accent-shape { fill: var(--crimson); }
  .contact {
    font-family: "Source Sans 3", "Myriad Pro", sans-serif;
    font-weight: 400;
  }
  .contact--company { font-size: 18px; }
  .contact--email, .contact--phone { font-size: 21px; }
  .on-light { fill: var(--crimson); }
  .on-dark { fill: var(--paper); }
  .brand-name {
    font-family: "Source Sans 3", "Myriad Pro", sans-serif;
    font-weight: 400;
  }
  .web-address {
    font-family: "Arimo", Arial, sans-serif;
    font-weight: 700;
    font-size: 11px;
    fill: var(--ink);
  }
</style>
</head>
<body>
<svg class="sheet" viewBox="0 0 1143 983" xmlns="http://www.w3.org/2000/svg">
  <defs>
    <clipPath id="sweep-card-shape">
      <rect x="43" y="3" width="527" height="299" rx="45"/>
    </clipPath>
  </defs>

  <!-- Card one: white with crimson sweep -->
  <g class="card card--sweep">
    <path class="accent-shape" clip-path="url(#sweep-card-shape)" d="M275 0 L575 0 L575 306 L375 306 C300 260 250 150 275 0 Z"/>
    <rect class="card-edge" x="43" y="3" width="527" height="299" rx="45"/>
    <g class="brand-lockup">
      <rect class="accent-shape" x="76" y="100" width="13" height="13"/>
      <text class="brand-name on-light" x="95" y="113" font-size="19">Lush Satchel</text>
    </g>
    <text class="web-address" x="88" y="186">lushsatchel.com.au</text>
    <text class="contact contact--company on-dark" x="330" y="181">Ferrow Communications</text>
    <text class="contact contact--email on-dark" x="338" y="212">xxxx@xxxxx. com</text>
    <text class="contact contact--phone on-dark" x="370" y="245">555•5555</text>
  </g>

  <!-- Card two: solid crimson -->
  <g class="card card--solid">
    <rect class="card-fill" x="23" y="365" width="526" height="300" rx="48"/>
    <text class="brand-name on-dark" x="40" y="440" font-size="56">Lush Satchel</text>
    <text class="contact contact--company on-dark" x="333" y="555">Ferrow Communications</text>
    <text class="contact contact--email on-dark" x="352" y="589">xxxx@xxxxx. com</text>
    <text class="contact contact--phone on-dark" x="432" y="625">555•5555</text>
  </g>

  <!-- Card three: white with small name -->
  <g class="card card--minimal">
    <rect class="card-edge" x="615" y="363" width="525" height="300" rx="48"/>
    <text class="brand-name on-light" x="1080" y="455" font-size="40" text-anchor="end">Lush Satchel</text>
    <text class="web-address" x="1046" y="479" text-anchor="end">lushsatchel.com.au</text>
    <text class="contact contact--company on-light" x="657" y="580">Ferrow Communications</text>
    <text class="contact contact--email on-light" x="660" y="600">xxxx@xxxxx. com</text>
    <text class="contact contact--phone on-light" x="661" y="627">555•5555</text>
  </g>

  <!-- Card four: white with large crimson name -->
  <g class="card card--statement">
    <rect class="card-edge" x="2" y="682" width="524" height="300" rx="48"/>
    <text class="brand-name on-light" x="20" y="770" font-size="56">Lush Satchel</text>
    <text class="contact contact--company on-light" x="318" y="859">Ferrow Communications</text>
    <text class="contact contact--email on-light" x="337" y="892">xxxx@xxxxx. com</text>
    <text class="contact contact--phone on-light" x="418" y="929">555•5555</text>
  </g>

</svg>
</body>
</html>
```